Corporate Business Card

Very professional, Modern, Not to busy, include phone address email, website
(253) 617-4930, 18761 52nd Avenue S, Kent, WA 98047, martin@plumlinegroup.com, varkoworks.com

Target Market(s)

Manufacturing

Industry/Entity Type

Aero, machining, manufacturing, Off road racing

Contact Information for Business Card

Phone, address email, website

```html
<!DOCTYPE html>
<html lang="en">
<head>
<meta charset="utf-8">
<title>Varko Works – Business Card</title>
<link rel="stylesheet" href="https://fonts.googleapis.com/css2?family=Saira:wght@400;600;700&display=swap">
<style>
  :root {
    --navy: #1a3670;
    --red: #d7262e;
    --white: #ffffff;
    --stage: #2b2b2d;
    --ink: #1a3670;
  }
  * { margin: 0; padding: 0; box-sizing: border-box; }
  html, body {
    width: 1200px; height: 1015px; overflow: hidden;
    background: var(--stage);
    font-family: "Saira", Arial, sans-serif;
  }
  .card {
    position: absolute; left: 220px;
    width: 760px; height: 434px;
    overflow: hidden;
  }
  .card--front { top: 54px; background: var(--navy); }
  .card--back  { top: 528px; background: var(--white); }

  .wordmark {
    position: absolute;
    font-weight: 700; letter-spacing: 3px;
    text-transform: uppercase; white-space: nowrap;
  }
  .card--front .wordmark {
    left: 0; right: 0; top: 150px; text-align: center;
    font-size: 78px; color: var(--white); line-height: 1;
  }
  .rule { position: absolute; height: 2px; }
  .card--front .rule { left: 190px; width: 380px; top: 262px; background: var(--white); }

  .card--back .wordmark {
    right: 48px; top: 48px; font-size: 48px; color: var(--navy); line-height: 1;
  }
  .card--back .rule { right: 48px; width: 330px; top: 116px; background: var(--navy); }

  .accent { position: absolute; left: 0; top: 140px; }
  .identity { position: absolute; left: 70px; top: 138px; }
  .identity__name {
    font-size: 28px; font-weight: 700; color: var(--navy);
    letter-spacing: 1px; line-height: 1; text-transform: uppercase;
  }
  .identity__title {
    font-size: 22px; font-weight: 400; color: var(--red); line-height: 1.2;
  }

  .contact { position: absolute; left: 150px; list-style: none; }
  .contact--lines { top: 236px; }
  .contact--address { top: 338px; }
  .contact li {
    display: flex; align-items: center; gap: 12px;
    font-size: 22px; color: var(--ink); line-height: 30px;
  }
  .contact--address li { align-items: flex-start; }
  .icon { width: 20px; height: 20px; flex: none; fill: var(--red); }
  .contact--address .icon { width: 22px; height: 28px; margin-top: 10px; }
</style>
</head>
<body>

<section class="card card--front" aria-label="Card front">
  <div class="wordmark">Varko Works</div>
  <div class="rule"></div>
</section>

<section class="card card--back" aria-label="Card back">
  <svg class="accent" width="62" height="58" viewBox="0 0 62 58" aria-hidden="true">
    <polygon points="0,0 22,0 12,58 0,58" fill="var(--navy)"/>
    <polygon points="34,0 62,0 52,58 24,58" fill="var(--red)"/>
  </svg>
  <div class="identity">
    <div class="identity__name">Daniel Reyes</div>
    <div class="identity__title">Managing Director</div>
  </div>

  <ul class="contact contact--lines">
    <li>
      <svg class="icon" viewBox="0 0 24 24" aria-hidden="true"><path d="M6.6 10.8a15.5 15.5 0 0 0 6.6 6.6l2.2-2.2c.3-.3.7-.4 1-.2 1.1.4 2.3.6 3.6.6.6 0 1 .4 1 1V20c0 .6-.4 1-1 1A17 17 0 0 1 3 4c0-.6.4-1 1-1h3.5c.6 0 1 .4 1 1 0 1.3.2 2.5.6 3.6.1.3 0 .7-.2 1z"/></svg>
      (253) 617-4930
    </li>
    <li>
      <svg class="icon" viewBox="0 0 24 24" aria-hidden="true"><path d="M2 5h20v14H2z" opacity=".0"/><path d="M2 5h20l-10 8z"/><path d="M2 7.5l10 7.8 10-7.8V19H2z"/></svg>
      martin@plumlinegroup.com
    </li>
    <li>
      <svg class="icon" viewBox="0 0 24 24" aria-hidden="true"><path d="M12 2a10 10 0 1 0 0 20 10 10 0 0 0 0-20zm6.9 6h-3a15 15 0 0 0-1.3-3.9A8 8 0 0 1 18.9 8zM12 4c.8 1.2 1.5 2.5 1.9 4h-3.8c.4-1.5 1.1-2.8 1.9-4zM4.3 14a8 8 0 0 1 0-4h3.4a16 16 0 0 0 0 4zm.8 2h3a15 15 0 0 0 1.3 3.9A8 8 0 0 1 5.1 16zm3-8h-3a8 8 0 0 1 4.3-3.9C8.8 5.3 8.4 6.6 8.1 8zM12 20c-.8-1.2-1.5-2.5-1.9-4h3.8c-.4 1.5-1.1 2.8-1.9 4zm2.3-6H9.7a14 14 0 0 1 0-4h4.6a14 14 0 0 1 0 4zm.3 5.9c.6-1.2 1-2.5 1.3-3.9h3a8 8 0 0 1-4.3 3.9zm1.7-5.9a16 16 0 0 0 0-4h3.4a8 8 0 0 1 0 4z"/></svg>
      www.varkoworks.com
    </li>
  </ul>

  <ul class="contact contact--address">
    <li>
      <svg class="icon" viewBox="0 0 22 28" aria-hidden="true"><path d="M11 0A11 11 0 0 0 0 11c0 8 11 17 11 17s11-9 11-17A11 11 0 0 0 11 0zm0 15a4 4 0 1 1 0-8 4 4 0 0 1 0 8z"/></svg>
      <span>18761 52nd Avenue S<br>Kent, WA 98047</span>
    </li>
  </ul>

  <div class="wordmark">Varko Works</div>
  <div class="rule"></div>
</section>

</body>
</html>
```